The Harbourlight Aid Trust needs a graphic of their innovation approach

What we need?
- we have designed a new innovation approach (see attached). An innovation approach is the process one goes through in order to design and launch a new product or service.
- This new graphic will be used in meetings to help others understand what innovation is and how we do it. It will also be used in training sessions and be the starting point for innovation training materials we are creating
- We have created this draft graphic by copying and pasting new words over another charities innovation process
- We would like you to use your design magic and create our very own innovation process graphic. We would like it to be neat, simple, non fussy, easy to understand /read and in line with our brand colours
Attached:
1. PowerPoint:
- Slide 1: our innovation process
- Slide 2 explanation of process to bring it to life
- Slide 3&4: brand colours
- Slide 5: inspiration / examples of other processes we like the look of
2. Typeface brand guidelines
We can't wait to see what you come up with! Thank you :)
Target Market(s)
internal employees
Industry/Entity Type
Charity
Colors
Designer to choose colors to be used in the design.
Look and feel
Each slider illustrates characteristics of the customer's brand and the style your logo design should communicate.

```html
<!DOCTYPE html>
<html lang="en">
<head>
<meta charset="utf-8">
<title>Innovation Approach — The Harbourlight Aid Trust</title>
<link rel="stylesheet" href="https://fonts.googleapis.com/css2?family=Arimo:wght@400;700&display=swap">
<style>
  :root {
    --discover-blue: #1a8fc4;
    --define-red: #e41f1a;
    --deliver-amber: #f5a61c;
    --ink-navy: #1c2d4e;
    --ring-grey: #e9eaec;
    --disc-light: #f4f4f4;
    --disc-shade: #e2e2e2;
    --paper: #ffffff;
  }
  html, body {
    margin: 0;
    padding: 0;
    width: 1200px;
    height: 999px;
    overflow: hidden;
    background: var(--paper);
  }
  .process-map {
    display: block;
    width: 1200px;
    height: 999px;
    font-family: "Arimo", Arial, sans-serif;
  }
  .track { fill: none; stroke-width: 14; stroke-linecap: butt; }
  .track--discover { stroke: var(--discover-blue); }
  .track--define { stroke: var(--define-red); }
  .track--deliver { stroke: var(--deliver-amber); }
  .ring { fill: none; stroke: var(--ring-grey); stroke-width: 14; }
  .stage-disc { fill: url(#disc-fill); }
  .stage-name { font-size: 25px; font-weight: 700; text-anchor: middle; }
  .stage-name--discover { fill: var(--discover-blue); }
  .stage-name--define { fill: var(--define-red); }
  .stage-name--deliver { fill: var(--deliver-amber); }
  .milestone { font-size: 22px; font-weight: 700; fill: var(--ink-navy); text-anchor: middle; }
  .step { font-size: 17px; font-weight: 700; }
  .step--discover { fill: var(--discover-blue); }
  .step--define { fill: var(--define-red); }
  .step--deliver { fill: var(--deliver-amber); }
  .pin--discover { fill: var(--discover-blue); stroke: var(--discover-blue); }
  .pin--define { fill: var(--define-red); stroke: var(--define-red); }
  .pin--deliver { fill: var(--deliver-amber); stroke: var(--deliver-amber); }
  .pin-stem { stroke-width: 6; }
  .icon-navy { fill: var(--ink-navy); }
  .icon-line { fill: none; stroke: var(--ink-navy); stroke-width: 2; stroke-linecap: round; }
</style>
</head>
<body>
<svg class="process-map" viewBox="0 0 1200 999" xmlns="http://www.w3.org/2000/svg" role="img" aria-label="Innovation approach: Discover, Define, Deliver">
  <defs>
    <radialGradient id="disc-fill" cx="50%" cy="40%" r="60%">
      <stop offset="0%" stop-color="var(--disc-light)"/>
      <stop offset="100%" stop-color="var(--disc-shade)"/>
    </radialGradient>
  </defs>

  <!-- background rings -->
  <circle class="ring" cx="367" cy="493" r="137"/>
  <circle class="ring" cx="587" cy="325" r="137"/>
  <circle class="ring" cx="808" cy="493" r="137"/>

  <!-- stage discs -->
  <circle class="stage-disc" cx="367" cy="493" r="108"/>
  <circle class="stage-disc" cx="587" cy="325" r="108"/>
  <circle class="stage-disc" cx="808" cy="493" r="108"/>

  <!-- tracks -->
  <path class="track track--discover" d="M20,493 H230 A137,137 0 0 0 504,493"/>
  <path class="track track--define" d="M504,493 C504,430 450,400 450,325 A137,137 0 0 1 724,325"/>
  <path class="track track--deliver" d="M724,325 C724,405 671,420 671,493 A137,137 0 0 0 945,493 H1155"/>

  <!-- pins -->
  <g class="pin--discover">
    <line class="pin-stem" x1="142" y1="452" x2="142" y2="493"/>
    <circle cx="142" cy="450" r="10"/>
    <line class="pin-stem" x1="443" y1="612" x2="460" y2="645"/>
    <circle cx="460" cy="646" r="10"/>
  </g>
  <g class="pin--define">
    <line class="pin-stem" x1="587" y1="150" x2="587" y2="190"/>
    <circle cx="587" cy="147" r="10"/>
  </g>
  <g class="pin--deliver">
    <line class="pin-stem" x1="724" y1="325" x2="765" y2="325"/>
    <circle cx="767" cy="325" r="10"/>
    <line class="pin-stem" x1="1005" y1="452" x2="1005" y2="493"/>
    <circle cx="1005" cy="450" r="10"/>
  </g>

  <!-- stage icons -->
  <g class="icon-discover" fill="none" stroke="var(--discover-blue)" stroke-width="4">
    <circle cx="382" cy="448" r="24"/>
    <path d="M394,434 A16,16 0 0 1 398,452" stroke-width="2"/>
    <line x1="364" y1="466" x2="330" y2="496" stroke-width="7" stroke-linecap="round"/>
  </g>
  <g class="icon-define" fill="none" stroke="var(--define-red)" stroke-width="4">
    <circle cx="592" cy="296" r="38"/>
    <circle cx="592" cy="296" r="26"/>
    <circle cx="592" cy="296" r="13"/>
    <path d="M594,294 L650,262 L656,272 L600,304 Z" fill="var(--define-red)" stroke="none"/>
  </g>
  <g class="icon-deliver">
    <path d="M808,432 a26,26 0 0 0 -16,46 v12 h32 v-12 a26,26 0 0 0 -16,-46 z" fill="none" stroke="var(--deliver-amber)" stroke-width="3"/>
    <rect x="796" y="492" width="24" height="8" fill="var(--deliver-amber)"/>
    <g stroke="var(--deliver-amber)" stroke-width="3" stroke-linecap="round">
      <line x1="808" y1="414" x2="808" y2="424"/>
      <line x1="787" y1="420" x2="792" y2="428"/>
      <line x1="829" y1="420" x2="824" y2="428"/>
    </g>
    <path d="M766,460 Q810,470 845,448 L840,440 L860,440 L850,458 L846,452 Q812,476 772,466 Z" fill="var(--deliver-amber)"/>
  </g>

  <text class="stage-name stage-name--discover" x="367" y="534">Discover</text>
  <text class="stage-name stage-name--define" x="587" y="368">Define</text>
  <text class="stage-name stage-name--deliver" x="808" y="534">Deliver</text>

  <!-- step labels along track -->
  <text class="step step--discover" transform="translate(222,596) rotate(40)">Insight</text>
  <text class="step step--discover" transform="translate(523,573) rotate(-72)">Ideate</text>
  <text class="step step--define" transform="translate(436,266) rotate(-66)">(Invalidate)</text>
  <text class="step step--define" transform="translate(666,175) rotate(40)">Test</text>
  <text class="step step--deliver" transform="translate(668,598) rotate(35)">Delivery Plan</text>

  <!-- milestone icons -->
  <g class="icon-challenge icon-navy">
    <path d="M118,402 L134,378 L142,388 L150,372 L168,402 Z"/>
    <line x1="150" y1="372" x2="150" y2="360" stroke="var(--ink-navy)" stroke-width="1.5"/>
    <path d="M150,360 L158,363 L150,366 Z"/>
  </g>
  <g class="icon-concepts">
    <path class="icon-navy" d="M574,96 C570,72 582,56 598,56 C614,56 622,70 620,84 L626,92 L620,94 V100 H608 V98 H582 V96 Z"/>
    <circle cx="594" cy="70" r="5" fill="none" stroke="#fff" stroke-width="2"/>
    <circle cx="605" cy="78" r="4" fill="none" stroke="#fff" stroke-width="2"/>
  </g>
  <g class="icon-solution">
    <path class="icon-line" d="M841,264 a12,12 0 0 0 -7,22 v8 h14 v-8 a12,12 0 0 0 -7,-22 z"/>
    <rect class="icon-navy" x="835" y="296" width="12" height="6"/>
    <g class="icon-line">
      <line x1="841" y1="250" x2="841" y2="256"/>
      <line x1="826" y1="256" x2="830" y2="260"/>
      <line x1="856" y1="256" x2="852" y2="260"/>
      <line x1="820" y1="270" x2="825" y2="270"/>
      <line x1="862" y1="270" x2="857" y2="270"/>
    </g>
  </g>
  <g class="icon-launch icon-navy">
    <path d="M1030,370 C1016,372 1000,384 994,398 L1002,406 C1016,400 1028,384 1030,370 Z"/>
    <path d="M994,388 L984,392 L990,400 Z"/>
    <path d="M1008,402 L1004,412 L996,406 Z"/>
    <path d="M992,402 L980,408 L986,396 Z"/>
  </g>
  <g class="icon-opportunity">
    <circle class="icon-navy" cx="541" cy="612" r="5"/>
    <path class="icon-navy" d="M532,628 a9,9 0 0 1 18,0 Z"/>
    <g class="icon-line" stroke-width="1.3">
      <line x1="541" y1="598" x2="541" y2="590"/>
      <line x1="541" y1="634" x2="541" y2="642"/>
      <line x1="525" y1="616" x2="517" y2="616"/>
      <line x1="557" y1="616" x2="565" y2="616"/>
      <line x1="530" y1="604" x2="524" y2="598"/>
      <line x1="552" y1="604" x2="558" y2="598"/>
      <line x1="530" y1="630" x2="524" y2="636"/>
      <line x1="552" y1="630" x2="558" y2="636"/>
    </g>
  </g>

  <!-- milestone labels -->
  <text class="milestone" x="142" y="428">Challenge</text>
  <text class="milestone" x="587" y="124">Concepts</text>
  <text class="milestone" x="842" y="330">Solution</text>
  <text class="milestone" x="1005" y="433">Launch</text>
  <text class="milestone" x="542" y="676">Opportunity</text>
  <text class="milestone" x="542" y="703">Statement</text>
</svg>
</body>
</html>
```